Tolvik Commercial Cleaning is lookong for a new business card design.

A fresh new design that's professional and stylish. We need a serious upgrade to our business cards. I have included pictures of our existing ones. Our clients include professional individuals and business owners. We woupdblike something professional and upbeat. Please have fun and see what you come uo with.

Target Market(s)

Property managers, business owners, facility managers and other similar professionals

Industry/Entity Type

Janitorial

Contact Information for Business Card

Name, cell, office number, email, web address

Font styles to use
Sans Serif

Colors

Designer to choose colors to be used in the design.

Requirements
Must have
• please use the green color in our logo
Nice to have
• Bar code
Should not have
• Address

```html
<!DOCTYPE html>
<html lang="en">
<head>
<meta charset="utf-8">
<title>Tolvik Commercial Cleaning — Business Card</title>
<link href="https://fonts.googleapis.com/css2?family=Open+Sans:wght@400;600;700&family=Quicksand:wght@700&display=swap" rel="stylesheet">
<style>
  :root {
    --backdrop: #333333;
    --card: #fcfdf3;
    --green: #3bb55a;
    --green-faint: #e6f2e0;
    --blue: #3a6aa8;
    --ink: #1e1e1e;
  }
  * { box-sizing: border-box; margin: 0; padding: 0; }
  html, body {
    width: 1200px; height: 780px; overflow: hidden;
    background: var(--backdrop);
  }
  .sheet {
    width: 1200px; height: 780px;
    display: flex; align-items: center; justify-content: center; gap: 40px;
  }
  .card {
    position: relative;
    width: 540px; height: 309px;
    background: var(--card);
    overflow: hidden;
    font-family: "Open Sans", Arial, sans-serif;
  }

  /* front side */
  .card--front { display: flex; align-items: center; justify-content: center; }
  .brand {
    display: flex; align-items: center; gap: 14px;
    font-family: "Quicksand", "Open Sans", sans-serif;
    font-weight: 700; color: var(--green);
  }
  .brand__dot {
    width: 22px; height: 22px; border-radius: 50%; background: var(--green); flex: none;
  }
  .card--front .brand__name { font-size: 34px; line-height: 1.1; max-width: 360px; }

  /* back side */
  .card--back .brand { position: absolute; left: 34px; top: 40px; }
  .card--back .brand__dot { width: 16px; height: 16px; }
  .card--back .brand__name { font-size: 24px; line-height: 1.15; max-width: 210px; }

  .backdrop-mark {
    position: absolute; right: -30px; top: 78px;
    font-family: "Quicksand", "Open Sans", sans-serif;
    font-weight: 700; font-size: 150px; line-height: 1;
    color: var(--green-faint);
  }
  .edge-bar {
    position: absolute; right: 0; top: 56px;
    width: 16px; height: 60px; background: var(--green);
  }
  .person {
    position: absolute; right: 30px; top: 62px; text-align: right;
  }
  .person__name { font-size: 25px; font-weight: 700; line-height: 1.1; color: var(--blue); }
  .person__first { color: var(--green); }
  .person__role { font-size: 14px; font-weight: 600; color: var(--ink); margin-top: 2px; }

  .contact {
    position: absolute; left: 34px; bottom: 30px;
    list-style: none;
  }
  .contact__item {
    display: flex; align-items: center; gap: 10px;
    font-size: 15px; color: var(--ink); line-height: 24px;
  }
  .contact__icon { width: 14px; height: 14px; flex: none; }
</style>
</head>
<body>
<main class="sheet">

  <section class="card card--front" aria-label="Card front">
    <div class="brand">
      <span class="brand__dot"></span>
      <span class="brand__name">Tolvik Commercial Cleaning</span>
    </div>
  </section>

  <section class="card card--back" aria-label="Card back">
    <div class="backdrop-mark" aria-hidden="true">Tolvik</div>

    <div class="brand">
      <span class="brand__dot"></span>
      <span class="brand__name">Tolvik Commercial Cleaning</span>
    </div>

    <span class="edge-bar"></span>
    <div class="person">
      <p class="person__name"><span class="person__first">Marco</span> Ellison</p>
      <p class="person__role">Director</p>
    </div>

    <ul class="contact">
      <li class="contact__item">
        <svg class="contact__icon" viewBox="0 0 16 16" aria-hidden="true"><path fill="#3bb55a" d="M3.5 1.5l2.4 2.6-1.3 1.8c.9 2 2.4 3.6 4.5 4.6l1.8-1.3 2.6 2.4-1.4 2.4C6.6 14 2 9.4 1.1 2.9z"/></svg>
        (555) 014-2290
      </li>
      <li class="contact__item">
        <svg class="contact__icon" viewBox="0 0 16 16" aria-hidden="true"><rect x="1" y="3" width="14" height="10" rx="1" fill="#3bb55a"/><path d="M1.5 3.5L8 9l6.5-5.5" fill="none" stroke="#fcfdf3" stroke-width="1.3"/></svg>
        marco@tolvikcleaning.com
      </li>
      <li class="contact__item">
        <svg class="contact__icon" viewBox="0 0 16 16" aria-hidden="true"><circle cx="8" cy="8" r="7" fill="#3bb55a"/><path d="M1 8h14M8 1c-3 3.5-3 10.5 0 14M8 1c3 3.5 3 10.5 0 14" fill="none" stroke="#fcfdf3" stroke-width="1"/></svg>
        www.tolvikcleaning.com
      </li>
    </ul>
  </section>

</main>
</body>
</html>
```